Post Disaster Temporary Housing Literature Review poster

Wanting a poster design for two Emergency Management conferences we have coming up. The information to be included in the poster is capturing the purpose, findings and recommendations from a post disaster temporary housing literature review looking at “What should government consider in order to improve planning and decision making for accommodation needs after a disaster, and to support people’s transition to stable housing?”
I’d like to enhance the visual appeal through including relevant images or graphic. I am also open to reducing the text if needed.
The government group I work with focuses on the social and human side of disaster recovery so keen for any images to reflect the human aspect and not focus solely on disasters or housing.
Government and NGO's

```html
<!DOCTYPE html>
<html lang="en">
<head>
<meta charset="utf-8">
<title>Post Disaster Temporary Housing Literature Review – Summary Report</title>
<link href="https://fonts.googleapis.com/css2?family=Poppins:wght@400;500;600;700;800&family=Oswald:wght@700&display=swap" rel="stylesheet">
<style>
  :root{
    --ink:#1b1b1d;
    --magenta:#c41fbd;
    --plum:#94208f;
    --pink:#fbdcf7;
    --pink-edge:#f5c4ef;
    --paper:#ffffff;
    --backdrop:#e6e6e6;
    --text:#1f1f1f;
    --rule:#cccccc;
  }
  *{box-sizing:border-box;margin:0;padding:0}
  html,body{width:746px;height:1200px;overflow:hidden}
  body{background:var(--backdrop);font-family:"Poppins",sans-serif;color:var(--text)}
  .poster{position:absolute;left:43px;top:0;width:660px;height:1200px;background:var(--paper);overflow:hidden}
  .abs{position:absolute}

  /* header */
  .masthead{left:0;top:0;width:370px;height:121px;background:var(--ink);color:#fff;padding:36px 0 0 32px}
  .masthead .line1{font-size:21px;letter-spacing:3.6px;font-weight:500;line-height:22px}
  .masthead .line2{font-size:28px;font-weight:800;color:var(--magenta);line-height:26px;letter-spacing:-.4px}
  .masthead .line3{font-size:21px;font-weight:800;letter-spacing:5.4px;line-height:24px}
  .hero{left:370px;top:0;width:290px;height:121px;background:linear-gradient(180deg,#5f7a86 0%,#8fa7ae 45%,#2a8fa4 78%,#e0c59a 100%)}

  .tab-summary{left:31px;top:121px;width:186px;height:38px;background:var(--plum);color:#fff;font-family:"Oswald",sans-serif;font-weight:700;font-size:26px;line-height:38px;text-align:center;border-radius:0 0 4px 4px;letter-spacing:-.3px}
  .tab-link{left:223px;top:121px;width:402px;height:38px;background:var(--plum);color:#fff;padding:4px 0 0 20px;border-radius:0 0 4px 4px}
  .tab-link .kicker{font-size:9.5px;letter-spacing:2.6px;line-height:13px}
  .tab-link .url{font-size:8.6px;font-weight:600;line-height:13px}

  /* purpose */
  .purpose-art{left:32px;top:172px;width:132px;height:138px;border-radius:10px;background:linear-gradient(160deg,#f4f1ee 0%,#4a4450 40%,#e4572e 62%,#c98a4c 82%,#f4f1ee 100%)}
  .purpose-icon{left:176px;top:176px}
  .h-purpose{left:210px;top:179px;font-size:22px;font-weight:800;color:var(--plum);letter-spacing:.2px}
  .purpose-body{left:176px;top:213px;width:446px;font-size:7.9px;line-height:9.5px}
  .purpose-body p+p{margin-top:5px}
  .purpose-body .question{color:var(--plum);font-weight:700}

  /* findings */
  .findings{left:28px;top:334px;width:599px;height:337px;background:var(--ink);border-radius:14px}
  .h-findings{left:57px;top:352px;display:flex;align-items:center;gap:14px;color:#fff;font-size:22px;font-weight:800}
  .card{background:var(--pink);border:2px solid var(--pink-edge);border-radius:8px;padding:9px 10px}
  .card-1{left:35px;top:396px;width:270px;height:266px}
  .card-2{left:309px;top:342px;width:311px;height:136px}
  .card-3{left:309px;top:483px;width:311px;height:179px}
  .card-head{display:flex;align-items:center;gap:12px;margin-bottom:6px}
  .num{width:30px;height:30px;border:2px solid var(--plum);outline:1px dashed #999;outline-offset:1px;color:var(--plum);font-size:21px;font-weight:800;display:flex;align-items:center;justify-content:center;flex:none;background:#fff}
  .card-title{color:var(--plum);font-size:12.2px;font-weight:700;line-height:15px}
  .card p{font-size:8.1px;line-height:9.3px}
  .card p+p{margin-top:8px}
  .card ul{list-style:none;margin:9px 0 0 0}
  .card li{position:relative;padding-left:17px;font-size:8.1px;line-height:9.3px;margin-bottom:8px}
  .card li::before{content:"";position:absolute;left:2px;top:1px;width:6px;height:6px;border-radius:50%;background:var(--plum)}

  /* recommendations */
  .rail{width:0;border-left:1px solid var(--rule)}
  .rec{display:flex;gap:6px}
  .rec-right{gap:16px}
  .rec .copy{width:222px}
  .rec-right .copy{width:226px}
  .badge{width:37px;height:37px;flex:none;border-radius:50%;border:1px dashed #555;padding:2px;background:#fff}
  .badge span{display:flex;width:100%;height:100%;border-radius:50%;align-items:center;justify-content:center}
  .badge .purple{background:var(--plum)}
  .badge .black{background:var(--ink)}
  .rec h3{font-size:11px;font-weight:700;line-height:13px;color:var(--ink)}
  .rec h3.accent{color:var(--plum)}
  .rec p{font-size:8px;line-height:9.4px;margin-top:2px}
  .research-list{display:grid;grid-template-columns:1fr 1fr;column-gap:10px;row-gap:6px;margin-top:7px;list-style:none}
  .research-list li{position:relative;padding-left:13px;font-size:5.9px;line-height:7px}
  .research-list li::before{content:"";position:absolute;left:2px;top:1px;width:5px;height:5px;border-radius:50%;background:var(--plum)}

  /* next steps */
  .next{left:35px;top:1042px;width:586px;height:44px;background:var(--plum);border-radius:3px;color:#fff;display:flex;align-items:center;padding:0 10px}
  .next-label{font-size:13px;font-weight:800;line-height:13px;margin:0 11px 0 12px}
  .next p{font-size:7.8px;line-height:9.4px}

  /* footer */
  .org{left:31px;top:1102px;display:flex;align-items:center;gap:16px}
  .org-mark{width:60px;height:60px;border-radius:50%;background:#2a9bd1}
  .org-name{font-size:12px;line-height:14px;color:#2f2f2f;font-weight:400}
  .contact-h{left:242px;top:1101px;font-size:13px;font-weight:800;color:var(--ink)}
  .contact-line{left:242px;top:1123px;font-size:7.9px;display:flex;gap:8px}
  .contact-line span::before{content:"● ";color:var(--plum);font-size:6px}
  .email-bar{left:239px;top:1143px;width:421px;height:23px;background:#000;color:#fff;display:flex;align-items:center;padding-left:8px;gap:10px;font-size:12.5px;letter-spacing:1.5px}
</style>
</head>
<body>
<main class="poster">

  <header class="abs masthead">
    <div class="line1">POST DISASTER</div>
    <div class="line2">TEMPORARY HOUSING</div>
    <div class="line3">LITERATURE REVIEW</div>
  </header>
  <div class="abs hero" role="img" aria-label="Illustration of a storm with a tornado and waves hitting a seaside house"></div>

  <div class="abs tab-summary">SUMMARY REPORT</div>
  <div class="abs tab-link">
    <div class="kicker">THE FULL REPORT IS AVAILABLE AT</div>
    <div class="url">https://library.recoveryinstitute.example.org/resources/community-recovery-group</div>
  </div>

  <section>
    <div class="abs purpose-art" role="img" aria-label="Illustration of field workers studying a volcano and the ground beneath it"></div>
    <svg class="abs purpose-icon" width="30" height="30" viewBox="0 0 30 30" aria-hidden="true">
      <circle cx="14" cy="16" r="12" fill="none" stroke="#1b1b1d" stroke-width="3" stroke-dasharray="4 2"/>
      <circle cx="14" cy="16" r="7" fill="none" stroke="#1b1b1d" stroke-width="2.5"/>
      <circle cx="14" cy="16" r="2.5" fill="#1b1b1d"/>
      <path d="M14 16 L27 3 M22 3 h5 v5" stroke="#1b1b1d" stroke-width="2.2" fill="none"/>
    </svg>
    <h2 class="abs h-purpose">PURPOSE</h2>
    <div class="abs purpose-body">
      <p>There are currently significant challenges in supporting displaced people with timely and equitable access to emergency and temporary accommodation and assisting them on a path to stable housing in the aftermath of a disaster. This report seeks to support agencies and decision makers to formulate and implement appropriate approaches to post-disaster housing, factoring in the scale of a disaster and varying community cohorts. The central research question underpinning this report is:</p>
      <p class="question" style="margin-top:3px">What should government consider in order to improve planning and decision making for accommodation needs after a disaster, and to support people’s transition to stable housing?</p>
      <p>The full report was commissioned by the Community Recovery Working Group (CRWG) and undertaken by Helen Marsh and Peter Quill through the Larkfield College of Applied Design (LCAD). The findings and recommendations may be utilised by stakeholders.</p>
    </div>
  </section>

  <section>
    <div class="abs findings"></div>
    <div class="abs h-findings">
      <svg width="34" height="34" viewBox="0 0 34 34" aria-hidden="true">
        <path d="M10 3 h14 l6 6 v22 h-20 z" fill="none" stroke="#c41fbd" stroke-width="2.5"/>
        <path d="M17 14 h9 M17 19 h9 M17 24 h9" stroke="#c41fbd" stroke-width="2.5"/>
        <circle cx="10" cy="18" r="6" fill="none" stroke="#c41fbd" stroke-width="2.5"/>
        <path d="M6 22 L1 27" stroke="#c41fbd" stroke-width="3"/>
      </svg>
      FINDINGS
    </div>

    <article class="abs card card-1">
      <div class="card-head"><div class="num">1</div><h3 class="card-title">Innovative approaches<br>to temporary housing</h3></div>
      <p>Innovative approaches to effective temporary housing practices are based upon the concept of resilient housing recovery, which has at least five dimensions: Wellbeing, Liveability, Sustainability, Community Connection, and Viability. This change of focus has two major implications:</p>
      <ul>
        <li>The planning of post-disaster housing and infrastructure programs needs to be become one of the priority strategies in pre-disaster preparation; and</li>
        <li>Strategies are needed to establish Temporary Housing as the first step in the design and construction of on-site Stable Housing to minimise the social, economic and environmental costs incurred when displaced people spend extended periods of time in Temporary Housing.</li>
      </ul>
      <p>These implications are explored through strategies and tools for pre-disaster planning and the development of a two-phase model for constructing Stable Housing through a “temporary to-permanent” construction strategy.</p>
    </article>

    <article class="abs card card-2">
      <div class="card-head"><div class="num">2</div><h3 class="card-title">Leading practice in disaster<br>housing recovery</h3></div>
      <p>The analysis of leading practices in housing recovery led to the development of a checklist of actions that could be used to identify appropriate actions by housing recovery officers and their agencies in providing and managing emergency and short-term accommodation and temporary housing. The checklist was developed from research and contains criteria for achieving eight categories of leading practice: Community Engagement &amp; Participation, Location, Safety, Health, Comfort &amp; Privacy, Cultural &amp; Special Needs, Community &amp; Connection, and Social &amp; Technical Support Services.</p>
    </article>

    <article class="abs card card-3">
      <div class="card-head"><div class="num">3</div><h3 class="card-title">A decision-making framework for<br>resilient housing recovery</h3></div>
      <p>The Framework seeks to integrate the steps in project management and to use the housing process as a lever for overall recovery. This involves aligning decisions at strategic and operational levels and managing the trade-offs between issues of location, tenure, housing types and procurement.</p>
      <p>There are nine such decision categories in the Framework: Consultation, Pre-Disaster Planning for Housing Recovery, Situation Analysis after a Disaster Event, Recognising Cohorts of Displaced People with Different Needs and Assets, Identifying and Selecting Housing Model Options; Providing AgencyWrap-Around Support Services; Using Housing Decisions to Promote Local Economic and Social Recovery, Program Design and Delivery, and Monitoring and Evaluation.</p>
    </article>
  </section>

  <section class="recommendations">
    <div class="abs rail" style="left:49px;top:718px;height:280px"></div>
    <div class="abs rail" style="left:346px;top:720px;height:280px"></div>

    <div class="abs rec" style="left:31px;top:692px">
      <div class="badge"><span class="purple"><svg width="16" height="16" viewBox="0 0 16 16"><rect x="3" y="2" width="10" height="12" fill="none" stroke="#fff" stroke-width="1.5"/><path d="M5 6h6M5 9h6" stroke="#fff"/></svg></span></div>
      <div class="copy"><h3>Terminology</h3><p>Develop a standard set of terminology to describe the phases and types of accommodation displaced people may access on the path to stable housing and to be adopted by State and Territory recovery agencies. The terms recommended for consideration are: Emergency and Short-Term Accommodation, Temporary Housing and Stable Housing.</p></div>
    </div>
    <div class="abs rec" style="left:31px;top:784px">
      <div class="badge"><span class="black"><svg width="16" height="16" viewBox="0 0 16 16"><rect x="3" y="2" width="9" height="12" fill="none" stroke="#fff" stroke-width="1.5"/><path d="M9 10l2 2 3-4" stroke="#fff" stroke-width="1.5" fill="none"/></svg></span></div>
      <div class="copy"><h3 class="accent">Principles</h3><p>Adopt common principles of leading practice in post-disaster housing recovery including community connection, wellbeing, liveability, viability, and sustainability, for deciding accommodation and support options for people.</p></div>
    </div>
    <div class="abs rec" style="left:31px;top:861px">
      <div class="badge"><span class="purple"><svg width="16" height="16" viewBox="0 0 16 16"><rect x="3" y="2" width="8" height="12" fill="none" stroke="#fff" stroke-width="1.5"/><path d="M11 8l3 1v3l-3 2-3-2V9z" fill="#fff"/></svg></span></div>
      <div class="copy"><h3>National Principles</h3><p>The Commonwealth and State/Territory governments should extend the agreed principles of disaster recovery to include principles of resilient recovery.</p></div>
    </div>
    <div class="abs rec" style="left:31px;top:919px">
      <div class="badge"><span class="black"><svg width="16" height="16" viewBox="0 0 16 16"><rect x="3" y="2" width="10" height="12" fill="none" stroke="#fff" stroke-width="1.5"/><path d="M5 6l1.5 1.5L9 5M5 11h6" stroke="#fff" stroke-width="1.3" fill="none"/></svg></span></div>
      <div class="copy"><h3 class="accent">Guidelines</h3><p>Develop resources and guidelines to support planning and operational response for post disaster temporary housing.</p></div>
    </div>
    <div class="abs rec" style="left:31px;top:979px">
      <div class="badge"><span class="purple"><svg width="16" height="16" viewBox="0 0 16 16"><circle cx="8" cy="8" r="5" fill="none" stroke="#fff" stroke-width="2.5" stroke-dasharray="3 1.5"/><circle cx="8" cy="8" r="1.8" fill="#fff"/></svg></span></div>
      <div class="copy"><h3>Capacity Building</h3><p>Develop capacity building resources and programs for State/Territory agencies and local governments to support pre planning for disaster temporary housing.</p></div>
    </div>

    <div class="abs rec rec-right" style="left:328px;top:692px">
      <div class="badge"><span class="purple"><svg width="16" height="16" viewBox="0 0 16 16"><path d="M4 14h6a3 3 0 0 0 0-7H6a3 3 0 0 0-2 7z" fill="#fff"/><path d="M11 11h4M11 13h4" stroke="#fff"/></svg></span></div>
      <div class="copy" style="padding-top:3px"><h3>Funding</h3><p>Recognise different cost implications of temporary housing programs including indirect costs. Develop funding streams to address the priority needs.</p></div>
    </div>
    <div class="abs rec rec-right" style="left:328px;top:749px">
      <div class="badge"><span class="black"><svg width="16" height="16" viewBox="0 0 16 16"><circle cx="9" cy="7" r="4.5" fill="none" stroke="#fff" stroke-width="1.6"/><path d="M6 10l-4 4" stroke="#fff" stroke-width="2"/></svg></span></div>
      <div class="copy" style="width:240px"><h3 class="accent">Further Research</h3><p>Undertake research into post disaster temporary housing topics such as:</p>
        <ul class="research-list">
          <li>Improving housing resilience through land-use planning and building codes.</li>
          <li>Utilisation of innovative construction technologies, materials and methods.</li>
          <li>Learnings from previous disasters on suitable approaches for different communities and contexts.</li>
          <li>Utilising permanent prefabricated housing modules that transition from temporary to permanent.</li>
        </ul>
      </div>
    </div>
    <div class="abs rec rec-right" style="left:328px;top:855px">
      <div class="badge"><span class="purple"><svg width="16" height="16" viewBox="0 0 16 16"><circle cx="8" cy="6" r="2.5" fill="#fff"/><path d="M3.5 13a4.5 4 0 0 1 9 0z" fill="#fff"/></svg></span></div>
      <div class="copy"><h3>Pilot Project</h3><p>Resource, trial and evaluate a pilot program to identify ways of achieving a two-phase approach to assisting home-owners and renter households into stable housing.</p></div>
    </div>
    <div class="abs rec rec-right" style="left:328px;top:912px">
      <div class="badge"><span class="black"><svg width="16" height="16" viewBox="0 0 16 16"><rect x="6" y="6" width="4" height="4" fill="#fff"/><rect x="2" y="2" width="3" height="3" fill="#fff"/><rect x="11" y="2" width="3" height="3" fill="#fff"/><rect x="2" y="11" width="3" height="3" fill="#fff"/><rect x="11" y="11" width="3" height="3" fill="#fff"/></svg></span></div>
      <div class="copy"><h3 class="accent">Decision Making Framework</h3><p>Adopt the outline of a Decision-Making Framework for Disaster Housing Recovery provided in this report to provide a basis for the development of tools that can be used by multiple stakeholders in housing recovery programs and projects across different parts of Australia.</p></div>
    </div>
    <div class="abs rec rec-right" style="left:328px;top:988px">
      <div class="badge"><span class="purple"><svg width="16" height="16" viewBox="0 0 16 16"><circle cx="8" cy="4" r="2" fill="#fff"/><path d="M2 8l6 2 6-2v5l-6 2-6-2z" fill="#fff"/></svg></span></div>
      <div class="copy"><h3>Capturing Learnings</h3><p>Establish a national repository of evaluation reports and support processes for regular cross-case analysis.</p></div>
    </div>
  </section>

  <section class="abs next">
    <svg width="22" height="20" viewBox="0 0 22 20" aria-hidden="true"><path d="M1 19h20V4h-5v5h-5v5H6v5z" fill="#fff"/><path d="M2 11L9 4M5 4h4v4" stroke="#fff" stroke-width="1.6" fill="none"/></svg>
    <div class="next-label">NEXT<br>STEPS</div>
    <p>The Community Recovery Working Group is partnering with Hazards Resilience Research Network to analyse previous post disaster temporary housing assistance and support mechanisms used in Australia. The project aims to provide national guidance on the design and implementation of temporary housing from the research and resources developed.</p>
  </section>

  <footer>
    <div class="abs org">
      <div class="org-mark"></div>
      <div class="org-name">Community Recovery<br>Working Group</div>
    </div>
    <h2 class="abs contact-h">FOR FURTHER INFORMATION CONTACT</h2>
    <div class="abs contact-line"><span>Morgan Ellery</span><span>National Consultant Disaster Recovery</span><span>Community Recovery Working Group</span></div>
    <div class="abs email-bar">
      <svg width="10" height="8" viewBox="0 0 10 8" aria-hidden="true"><rect width="10" height="8" fill="#c41fbd"/><path d="M0 0l5 4 5-4" stroke="#000" fill="none"/></svg>
      morgan.ellery@recoveryoffice.example.org
    </div>
  </footer>

</main>
</body>
</html>
```